BrindleStaffing Business Card Design

We are a staffing company finding positions for dedicated nurses and physicians.

Target Market(s)

Business Professionals

Industry/Entity Type

Staffing

Contact Information for Business Card

Gordon Pratley
Chairman
417 39th Avenue South
SAINT PETERSBURG FL 33712
813-555-4172 Mobile
813-555-8036 Fax
gpratley@brindlestaffing.com
www.brindlestaffing.com

Font styles to use
Sans Serif

Colors
fbee3e
f04a50
f37122

Requirements
Must have
• Logo Attached, see colors below. We'd like to see Yellow, Orange and Red.

```html
<!DOCTYPE html>
<html lang="en">
<head>
<meta charset="utf-8">
<title>BrindleStaffing Business Card</title>
<link href="https://fonts.googleapis.com/css2?family=Poppins:wght@400;500;600&family=Lato:wght@400&display=swap" rel="stylesheet">
<style>
  :root {
    --backdrop: #2b2b2b;
    --card: #1c1c1d;
    --card-edge: #202022;
    --ink: #ffffff;
    --ink-soft: #e6e6e6;
    --rule: #7a7a7a;
    --pattern: #29292b;
    --brand-yellow: #fbee3e;
    --brand-orange: #f37122;
    --brand-red: #f04a50;
  }
  * { margin: 0; padding: 0; box-sizing: border-box; }
  html, body {
    width: 1200px; height: 1108px; overflow: hidden;
    background: var(--backdrop);
  }
  .stage {
    position: relative; width: 1200px; height: 1108px;
    display: flex; justify-content: center; align-items: center; gap: 80px;
  }
  .card {
    position: relative; width: 400px; height: 700px;
    background: var(--card); border-radius: 26px;
    box-shadow: 0 18px 40px rgba(0,0,0,.45);
    color: var(--ink); overflow: hidden;
  }
  .brand-stripe {
    position: absolute; left: 0; right: 0; bottom: 0; height: 10px;
    display: flex;
  }
  .brand-stripe span { flex: 1; }
  .brand-stripe .yellow { background: var(--brand-yellow); }
  .brand-stripe .orange { background: var(--brand-orange); }
  .brand-stripe .red { background: var(--brand-red); }
  .wordmark {
    display: flex; justify-content: center; align-items: center; gap: 8px;
    font-family: "Poppins", sans-serif; font-weight: 600;
    font-size: 44px; letter-spacing: -1.5px; color: var(--ink);
    line-height: 1;
  }
  .wordmark-dot {
    width: 12px; height: 12px; border-radius: 50%;
    background: var(--brand-orange); flex: none;
  }
  .card-front .wordmark { position: absolute; top: 190px; left: 0; right: 0; }
  .details {
    position: absolute; top: 372px; left: 50px; right: 50px; text-align: center;
  }
  .person-name {
    font-family: "Poppins", sans-serif; font-weight: 500; font-size: 29px;
    line-height: 36px; letter-spacing: .3px;
  }
  .person-title {
    font-family: "Poppins", sans-serif; font-weight: 400; font-size: 15px;
    line-height: 22px; letter-spacing: 2px; text-transform: uppercase;
    color: var(--brand-yellow); margin: 2px 0 10px;
  }
  .icon-rule { display: flex; align-items: center; gap: 8px; margin-bottom: 12px; }
  .icon-rule .line { flex: 1; height: 1px; background: var(--rule); }
  .icon-rule svg { width: 24px; height: 24px; flex: none; }
  .contact-lines, .address {
    font-family: "Lato", sans-serif; font-size: 18px; line-height: 26px;
    color: var(--ink-soft);
  }
  .contact-label { color: var(--brand-orange); }
  .divider { height: 1px; background: var(--rule); margin: 10px 0 8px; }
  .pattern-field {
    position: absolute; inset: 0;
    background: linear-gradient(160deg, var(--pattern) 0%, var(--card-edge) 45%, var(--card) 75%);
  }
  .card-back .wordmark { position: absolute; bottom: 130px; left: 0; right: 0; }
</style>
</head>
<body>
<main class="stage">
  <section class="card card-front">
    <div class="wordmark">BrindleStaffing<span class="wordmark-dot"></span></div>
    <div class="details">
      <p class="person-name">Gordon Pratley</p>
      <p class="person-title">Chairman</p>
      <div class="icon-rule">
        <span class="line"></span>
        <svg viewBox="0 0 24 24" aria-label="phone"><circle cx="12" cy="12" r="12" fill="#fbee3e"/><path d="M8 6.5c.6-.4 1.3-.3 1.6.3l1 1.8c.3.5.1 1.1-.3 1.4l-.7.5c.5 1.3 1.5 2.4 2.8 3l.6-.6c.4-.4 1-.5 1.4-.2l1.7 1.1c.6.4.6 1.1.2 1.6l-.8.9c-.7.7-2 .8-3.3.1-2.4-1.3-4.3-3.4-5.2-5.9-.4-1.2-.2-2.4.5-3z" fill="#1c1c1d"/></svg>
        <svg viewBox="0 0 24 24" aria-label="email"><circle cx="12" cy="12" r="12" fill="#f37122"/><rect x="6" y="8" width="12" height="8.5" rx="1" fill="#1c1c1d"/><path d="M6.5 8.6 12 12.8l5.5-4.2" stroke="#f37122" stroke-width="1.2" fill="none"/></svg>
        <svg viewBox="0 0 24 24" aria-label="website"><circle cx="12" cy="12" r="12" fill="#f04a50"/><circle cx="12" cy="12" r="6" fill="none" stroke="#1c1c1d" stroke-width="1.4"/><ellipse cx="12" cy="12" rx="2.6" ry="6" fill="none" stroke="#1c1c1d" stroke-width="1.2"/><path d="M6 12h12" stroke="#1c1c1d" stroke-width="1.2"/></svg>
        <span class="line"></span>
      </div>
      <div class="contact-lines">
        <p>813-555-4172 <span class="contact-label">Mobile</span></p>
        <p>813-555-8036 <span class="contact-label">Fax</span></p>
        <p>gpratley@brindlestaffing.com</p>
        <p>www.brindlestaffing.com</p>
      </div>
      <div class="divider"></div>
      <div class="address">
        <p>417 39th Avenue South</p>
        <p>SAINT PETERSBURG FL 33712</p>
      </div>
    </div>
    <div class="brand-stripe"><span class="yellow"></span><span class="orange"></span><span class="red"></span></div>
  </section>

  <section class="card card-back">
    <div class="pattern-field" role="img" aria-label="Faint tone-on-tone repeated brand pattern"></div>
    <div class="wordmark">BrindleStaffing<span class="wordmark-dot"></span></div>
    <div class="brand-stripe"><span class="yellow"></span><span class="orange"></span><span class="red"></span></div>
  </section>
</main>
</body>
</html>
```